Tech business card design

We need an amazing business card design for our new business 'Pexla' a marketing tech startup based in Sydney, Australia. We provide an online marketplace for businesses to search and buy advertising media, connect with service providers and learn more about marketing. We wish to communicate 'cool tech', reliability and professionalism and design based around our logo.

Target Market(s)

Business Owners

Contact Information for Business Card

Name
Position
Email Address
Website
Phone Number

Font styles to use
Other font styles liked:
• Avenir & Avenir Next

Colors

Designer to choose colors to be used in the design.

```html
<!DOCTYPE html>
<html lang="en">
<head>
<meta charset="utf-8">
<title>Pexla business card</title>
<link href="https://fonts.googleapis.com/css2?family=Lato:wght@400;700;900&display=swap" rel="stylesheet">
<style>
  :root {
    --navy: #0e0e3c;
    --navy-line: #1c1c5a;
    --white: #ffffff;
    --backdrop: #8c4f22;
    --card-shadow: rgba(0, 0, 0, 0.45);
  }
  html, body {
    margin: 0;
    width: 1200px;
    height: 900px;
    overflow: hidden;
    background: var(--backdrop);
    font-family: "Lato", sans-serif;
  }
  .canvas {
    position: relative;
    width: 1200px;
    height: 900px;
  }
  .card {
    position: absolute;
    box-shadow: 3px 4px 6px var(--card-shadow);
    overflow: hidden;
  }
  .card-front {
    left: 330px;
    top: 90px;
    width: 555px;
    height: 343px;
    background: var(--navy);
  }
  .card-back {
    left: 330px;
    top: 469px;
    width: 558px;
    height: 343px;
    background: var(--white);
  }
  .wordmark {
    position: absolute;
    margin: 0;
    font-family: "Lato", sans-serif;
    font-weight: 900;
    line-height: 1;
    letter-spacing: 1px;
  }
  .card-front .wordmark {
    left: 150px;
    top: 128px;
    font-size: 88px;
    color: var(--white);
  }
  .card-back .wordmark {
    left: 40px;
    top: 82px;
    font-size: 82px;
    color: var(--navy);
  }
  .wave {
    position: absolute;
    left: 0;
    top: 0;
    width: 558px;
    height: 343px;
  }
  .contact {
    position: absolute;
    right: 35px;
    top: 201px;
    text-align: right;
    color: var(--white);
  }
  .contact-name {
    margin: 0;
    font-size: 18px;
    font-weight: 700;
    letter-spacing: 0.5px;
    line-height: 22px;
    text-transform: uppercase;
  }
  .contact-role {
    margin: 0 0 16px;
    font-size: 16px;
    font-weight: 400;
    line-height: 18px;
  }
  .contact-list {
    list-style: none;
    margin: 0;
    padding: 0;
    font-size: 15px;
    line-height: 20.5px;
  }
  .contact-list li {
    display: flex;
    justify-content: flex-end;
    align-items: center;
    gap: 5px;
  }
  .contact-icon {
    width: 12px;
    height: 12px;
    fill: var(--white);
  }
</style>
</head>
<body>
<main class="canvas">
  <section class="card card-front" aria-label="Card front">
    <p class="wordmark">pexla</p>
  </section>

  <section class="card card-back" aria-label="Card back">
    <p class="wordmark">pexla</p>
    <svg class="wave" viewBox="0 0 558 343" aria-hidden="true">
      <path fill="var(--navy-line)" d="M0 190 C60 235 150 248 250 214 C340 182 410 140 470 144 C515 147 545 170 558 200 L558 343 L0 343 Z"/>
      <path fill="var(--navy)" d="M0 202 C60 247 150 260 250 226 C340 194 410 152 470 156 C515 159 545 182 558 212 L558 343 L0 343 Z"/>
      <path fill="none" stroke="var(--white)" stroke-width="3.5" d="M0 200 C60 245 150 258 250 224 C340 192 410 150 470 154 C515 157 545 180 558 210"/>
    </svg>
    <div class="contact">
      <p class="contact-name">Daniel Harper</p>
      <p class="contact-role">Managing Director</p>
      <ul class="contact-list">
        <li>044-987 654 321
          <svg class="contact-icon" viewBox="0 0 12 12" aria-hidden="true"><path d="M1 4 Q6 0 11 4 L9.5 5.5 L8 4.5 L8 3.5 Q6 3 4 3.5 L4 4.5 L2.5 5.5 Z M3 6 L9 6 L10.5 11 L1.5 11 Z"/></svg>
        </li>
        <li>hello@pexlamail.com
          <svg class="contact-icon" viewBox="0 0 12 12" aria-hidden="true"><path d="M0.5 2.5 H11.5 V9.5 H0.5 Z M1.5 3.3 L6 6.8 L10.5 3.3" stroke="var(--navy)" stroke-width="0.9"/></svg>
        </li>
        <li>www.pexlasite.com
          <svg class="contact-icon" viewBox="0 0 12 12" aria-hidden="true"><circle cx="6" cy="6" r="5.5"/><path d="M0.5 6 H11.5 M6 0.5 Q3 6 6 11.5 M6 0.5 Q9 6 6 11.5" fill="none" stroke="var(--navy)" stroke-width="0.8"/></svg>
        </li>
      </ul>
    </div>
  </section>
</main>
</body>
</html>
```